Create modern and sleek business card for luxury real estate company

We're a "boutique" real estate office looking for a design that gets across a highly modern luxury brand. Blacks and whites are probably the best colors unless we try a silver foil for the logo. I've attached a version of our current logo here. I'd like to swap out the current font on there with Gotham Light Regular.

I'm looking to have one side of the card have the logo with the space for our agents info on the other side.

Target Market(s)

Young professionals in a "luxury" headspace

Industry/Entity Type

Real estate

Contact Information for Business Card

A place for agent name, cell number, website. The slogan "Simply Rethinking Real Estate".

Font styles to use
Other font styles liked:
• Gotham Regular

Colors

Designer to choose only greyscale colors for use in the design.

Requirements
Must have
• Matte black as the background color. Clean lines and use of contrast. A specific design aspect that will use silver foil.
Nice to have
• Up in the air on integrating a QR code
Should not have
• Any houses or other real estate related design (ex: a clip art house)

```html
<!DOCTYPE html>
<html lang="en">
<head>
<meta charset="utf-8">
<title>Meridian Estates — Business Card</title>
<link rel="stylesheet" href="https://fonts.googleapis.com/css2?family=Cinzel:wght@600;700&family=Lato:wght@400&display=swap">
<style>
  :root {
    --backdrop: #2a2a2a;
    --card-black: #0d0d0d;
    --card-edge: #1c1c1c;
    --silver: #f1f1f1;
    --silver-soft: #cfcfcf;
    --shadow: rgba(0,0,0,0.55);
  }
  * { margin: 0; padding: 0; box-sizing: border-box; }
  html, body {
    width: 1200px; height: 866px; overflow: hidden;
    background: var(--backdrop);
  }
  .stage {
    width: 1200px; height: 866px;
    display: flex; flex-direction: column; align-items: center; justify-content: center;
    gap: 40px;
  }
  .card {
    position: relative;
    width: 600px; height: 343px;
    background: radial-gradient(ellipse at 40% 35%, var(--card-edge) 0%, var(--card-black) 70%);
    box-shadow: 0 14px 30px var(--shadow);
    color: var(--silver);
    overflow: hidden;
  }
  .card__texture {
    position: absolute; inset: 0;
    background: radial-gradient(circle at 35% 40%, rgba(255,255,255,0.05) 0%, rgba(255,255,255,0) 55%);
  }
  .brand {
    position: absolute;
    display: flex; align-items: center; gap: 16px;
  }
  .brand__circle {
    width: 74px; height: 74px; border-radius: 50%;
    border: 3px solid var(--silver);
    flex: none;
  }
  .brand__name {
    font-family: "Cinzel", serif; font-weight: 600;
    font-size: 34px; line-height: 1.05; letter-spacing: 2px;
    color: var(--silver);
  }
  .card--front .brand { left: 50%; top: 50%; transform: translate(-50%, -50%); }

  .card--back .brand { left: 282px; top: 48px; }
  .card--back .brand__circle { width: 62px; height: 62px; }
  .card--back .brand__name { font-size: 28px; }

  .agent {
    position: absolute; left: 34px; top: 62px;
  }
  .agent__name {
    font-family: "Cinzel", serif; font-weight: 700;
    font-size: 17px; letter-spacing: 1px;
  }
  .agent__title {
    font-family: "Lato", sans-serif; font-size: 14px;
    color: var(--silver-soft); margin-top: 2px;
  }
  .contact { list-style: none; margin-top: 14px; }
  .contact__item {
    display: flex; align-items: center; gap: 8px;
    font-family: "Lato", sans-serif; font-size: 14px; line-height: 21px;
  }
  .contact__icon { width: 13px; height: 13px; flex: none; }
  .divider {
    position: absolute; left: 190px; top: 142px;
    width: 380px; height: 1px; background: var(--silver-soft);
  }
  .address {
    position: absolute; right: 34px; bottom: 40px;
    font-family: "Lato", sans-serif; font-size: 15px; line-height: 21px;
    text-align: right;
  }
</style>
</head>
<body>
<main class="stage">
  <section class="card card--front" aria-label="Card front">
    <div class="card__texture" role="img" aria-label="Fine dotted matte texture"></div>
    <div class="brand">
      <span class="brand__circle"></span>
      <span class="brand__name">Meridian<br>Estates</span>
    </div>
  </section>

  <section class="card card--back" aria-label="Card back">
    <div class="card__texture" role="img" aria-label="Fine dotted matte texture"></div>
    <div class="agent">
      <p class="agent__name">DANIEL HART</p>
      <p class="agent__title">Managing Director</p>
      <ul class="contact">
        <li class="contact__item">
          <svg class="contact__icon" viewBox="0 0 16 16" fill="none" stroke="currentColor" stroke-width="1.6"><path d="M4 1.5l2.5 3-1.5 1.5c.8 2 2.5 3.7 4.5 4.5l1.5-1.5 3 2.5-1.5 2.5C7 14 2 9 1.5 3z"/></svg>
          044-987 654 321
        </li>
        <li class="contact__item">
          <svg class="contact__icon" viewBox="0 0 16 16" fill="none" stroke="currentColor" stroke-width="1.6"><rect x="1" y="3" width="14" height="10"/><path d="M1 3l7 6 7-6"/></svg>
          hello@meridianestates.com
        </li>
        <li class="contact__item">
          <svg class="contact__icon" viewBox="0 0 16 16" fill="none" stroke="currentColor" stroke-width="1.4"><circle cx="8" cy="8" r="6.5"/><ellipse cx="8" cy="8" rx="3" ry="6.5"/><path d="M1.5 8h13"/></svg>
          www.meridianestates.com
        </li>
      </ul>
    </div>
    <div class="brand">
      <span class="brand__circle"></span>
      <span class="brand__name">Meridian<br>Estates</span>
    </div>
    <div class="divider"></div>
    <p class="address">118, Harbor Lane<br>Westbrook, 20817</p>
  </section>
</main>
</body>
</html>
```